Personal website for my flying adventures

It is the website for my personal flying adventures.

1. I flew around the world in 2011 and became the first Chinese citizen ever flying the single engine airplane around the world in the history and also the first ever to land the single engine airplane in Halvern Ridge airport.
2. I am organizing the "Copper Kestrels Aerobatic Flying Team" in China
3. I am sharing my flying experiences regularly
4. I am writing the book about flying around the world.

Visit: www.lutanmo.com and www.tanmoskyloop.com for more information and pictures on my flying activities. Need connect two websites together well.

Target Market(s)

Young pilots

Industry/Entity Type

Airport

Requirements
Must have
• Must have the logo of "Tanmo Sky Loop"
• Must have the logo of "Copper Kestrels"
• Must have my flying pictures

```html
<!DOCTYPE html>
<html lang="zh">
<head>
<meta charset="utf-8">
<title>Lu Tanmo — Flying</title>
<link rel="stylesheet" href="https://fonts.googleapis.com/css2?family=Jost:wght@300;400;500;600&family=Noto+Sans+SC:wght@400;500;700&family=Ma+Shan+Zheng&display=swap">
<style>
  :root{
    --black:#000;
    --gold:#e8c66a;
    --gold-text:#f2c94c;
    --badge:#8a8070;
    --white:#fff;
    --muted:#8c8c8c;
    --sky-deep:#0a3aa8;
    --sky-mid:#2a66cf;
    --sky-light:#9cbfe9;
    --haze:#dfe8f6;
    --steel:#8fa6cf;
  }
  *{margin:0;padding:0;box-sizing:border-box}
  html,body{width:1200px;height:689px;overflow:hidden;background:var(--black)}
  body{position:relative;font-family:"Jost",sans-serif;color:var(--white)}

  .site-header{position:absolute;top:0;left:0;width:1200px;height:75px;background:var(--black)}
  .journey{position:absolute;left:31px;top:29px;font-size:13px;font-weight:600;color:var(--gold-text)}
  .route{position:absolute;left:142px;top:21px;width:149px;height:35px;background:var(--badge);
    display:flex;align-items:center;justify-content:center;gap:6px;font-size:19px;font-weight:600;color:var(--white)}
  .route svg{width:26px;height:18px}
  .brand{position:absolute;left:549px;top:23px;font-size:21px;font-weight:600;letter-spacing:.5px}
  .main-nav{position:absolute;right:85px;top:29px;display:flex;gap:15px;font-size:13px;font-weight:400;text-transform:uppercase;letter-spacing:-.2px}
  .main-nav a{color:var(--white);text-decoration:none}
  .main-nav a.is-active{color:var(--gold-text)}
  .lang{position:absolute;right:25px;top:24px;width:36px;height:25px;border:1px solid var(--gold-text);
    font-family:"Noto Sans SC",sans-serif;font-size:12px;display:flex;align-items:center;justify-content:center}

  .site-bar{position:absolute;top:75px;left:0;width:1200px;height:18px;background:var(--gold);
    display:flex;justify-content:flex-end;gap:21px;padding-right:28px;align-items:center}
  .site-bar a{color:#1a1a1a;text-decoration:none;font-family:"Noto Sans SC",sans-serif;font-size:11px;font-weight:500}

  .hero{position:absolute;top:93px;left:0;width:1200px;height:559px;overflow:hidden}
  .hero-photo{position:absolute;inset:0;
    background:
      radial-gradient(ellipse 300px 200px at 790px 300px,var(--haze) 0%,rgba(200,215,240,.75) 40%,rgba(160,185,230,0) 80%),
      radial-gradient(ellipse 420px 120px at 930px 330px,rgba(143,166,207,.55) 0%,rgba(143,166,207,0) 80%),
      radial-gradient(ellipse 520px 220px at 250px 520px,rgba(200,220,245,.45) 0%,rgba(200,220,245,0) 80%),
      linear-gradient(115deg,var(--sky-deep) 0%,var(--sky-mid) 42%,var(--sky-light) 100%)}
  .hero-copy{position:absolute;left:162px;top:104px;width:330px}
  .hero-title{font-family:"Noto Sans SC",sans-serif;font-size:57px;font-weight:500;line-height:1;letter-spacing:1px}
  .hero-name{font-family:"Ma Shan Zheng",cursive;font-size:52px;color:var(--gold-text);line-height:1;margin-top:6px}
  .hero-text{font-family:"Noto Sans SC",sans-serif;font-size:12.5px;font-weight:700;line-height:23px;margin-top:8px;letter-spacing:.6px}
  .hero-text span{display:block;white-space:nowrap}
  .slide-arrow{position:absolute;top:240px;width:37px;height:37px;background:var(--black);
    display:flex;align-items:center;justify-content:center}
  .slide-arrow svg{width:10px;height:14px}
  .slide-arrow--prev{left:0}
  .slide-arrow--next{right:0}

  .site-footer{position:absolute;top:652px;left:0;width:1200px;height:37px;background:var(--black)}
  .social{position:absolute;left:544px;top:11px;display:flex;gap:22px;font-size:12px;font-weight:300;text-transform:uppercase}
  .social a{color:var(--white);text-decoration:none}
  .copyright{position:absolute;right:35px;top:13px;font-size:10.5px;font-weight:300;color:var(--muted)}
</style>
</head>
<body>
  <header class="site-header">
    <div class="journey">Current Journey</div>
    <div class="route">MEM
      <svg viewBox="0 0 26 18" aria-hidden="true"><path fill="#fff" d="M1 8h9L6 1h3l7 7h7a2 1 0 0 1 0 2h-7l-7 7H6l4-7H1z"/></svg>
      DCA</div>
    <div class="brand">LU TANMO</div>
    <nav class="main-nav">
      <a href="#">About</a><a href="#" class="is-active">Photos</a><a href="#">Journal</a><a href="#">Itinerary</a>
    </nav>
    <div class="lang">中文</div>
  </header>

  <nav class="site-bar">
    <a href="#">环球飞行中文网站</a>
    <a href="#">Tanmo Sky Loop</a>
    <a href="#">卢坦墨飞行网站</a>
  </nav>

  <section class="hero">
    <div class="hero-photo" role="img" aria-label="Photo of a passenger jet climbing overhead through a bright blue sky, with a thin contrail crossing behind it"></div>
    <div class="hero-copy">
      <h1 class="hero-title">快乐飞翔</h1>
      <div class="hero-name">卢坦墨</div>
      <p class="hero-text">
        <span>我热爱飞行，并享受飞行带来的快乐及方便。在中国，大</span>
        <span>家认为私人飞行是富人玩的游戏。而在美国，是综合国力</span>
        <span>的表现。随着中国通用航空的发展，每个中国人都将享受</span>
        <span>飞行的自由和权利。我希望通过我的飞行热爱，推动中国</span>
      </p>
    </div>
    <a class="slide-arrow slide-arrow--prev" href="#" aria-label="Previous"><svg viewBox="0 0 10 14"><path d="M8 1 2 7l6 6" stroke="#fff" stroke-width="2.5" fill="none"/></svg></a>
    <a class="slide-arrow slide-arrow--next" href="#" aria-label="Next"><svg viewBox="0 0 10 14"><path d="M2 1l6 6-6 6" stroke="#f2c94c" stroke-width="2.5" fill="none"/></svg></a>
  </section>

  <footer class="site-footer">
    <div class="social"><a href="#">Friendwall</a><a href="#">Chirpline</a></div>
    <div class="copyright">Copyright 2013 LuTanmo All rights reserved.</div>
  </footer>
</body>
</html>
```